Electric mountain bike tours nz

We are an Electric Mountain bike tour company in New Zealand. We will be offering bike rental and guided tours around the Nelson region in New Zealand. I want our website to represent both Mountain biking and New Zealand with the colours layout and features. We want tabs for the following:
-1 about us
-2 what we offer
-3 bookings/contact
Under the about us tab will be who we are as a a company. I want the ability to add videos to each of these tabs as we move foward with videos of the tracks we will be riding. I want the website to be editable so I can add and remove videos/photos myself. Also "our bikes" will be under this tab.
Under the what we offer tab will be
-1 bike rental and pricing
-2 guided tours and pricing
-3 recommended package deals.
I want to able to put the tracks under the guided tours tab and select beginner/ intermediate/advanced and have the tracks in each of the following to match the rider level. Also to be able to have a small video of the track would be great in this section.
Bookings and contact tab
(Further information for this tab to be updated soon)
Coded - Design and coding required
1 page
- Silver ferns, kiwi, mountains

```html
<!DOCTYPE html>
<html lang="en">
<head>
<meta charset="utf-8">
<title>Ridgevolt – E-Mountain Bike Tours</title>
<link href="https://fonts.googleapis.com/css2?family=Montserrat:wght@400;500;600;700;800&family=Open+Sans:wght@400;600&display=swap" rel="stylesheet">
<style>
:root{
  --orange:#f15a1f;
  --black:#000;
  --ink:#3a3a3a;
  --muted:#6b6b6b;
  --light:#f2f2f2;
  --white:#fff;
  --label:rgba(30,30,30,.85);
}
*{box-sizing:border-box;margin:0;padding:0}
html,body{width:1200px;height:3636px;overflow:hidden;background:var(--white)}
body{position:relative;font-family:"Open Sans",Arial,sans-serif;color:var(--ink)}
.abs{position:absolute}
.head{left:0;top:0;width:1200px;height:109px;background:var(--black);z-index:2}
.brand-badge{position:absolute;border-radius:50%;background:var(--black);border:6px solid var(--white);display:flex;align-items:center;justify-content:center;color:var(--white);font-family:"Montserrat",sans-serif;font-weight:800;letter-spacing:1px}
.head .brand-badge{left:85px;top:0;width:180px;height:180px;font-size:28px;border:none;box-shadow:0 0 0 0 transparent}
.nav{position:absolute;top:48px;left:590px;display:flex;gap:0;font-family:"Montserrat",sans-serif;font-size:13px;font-weight:600;color:var(--white);text-transform:uppercase}
.nav a{color:var(--white);text-decoration:none;position:absolute;white-space:nowrap}
.nav .active{color:#bbb;font-weight:500}
.hero{left:0;top:109px;width:1200px;height:570px;background:linear-gradient(180deg,#f3ddb8 0%,#e6c79a 35%,#a89c8c 60%,#5a4e42 80%,#3b302a 100%)}
.hero h1{position:absolute;left:85px;top:250px;font-family:"Montserrat",sans-serif;font-weight:800;font-size:82px;color:var(--orange);letter-spacing:1px}
.hero p{position:absolute;left:85px;top:368px;width:520px;font-family:"Montserrat",sans-serif;font-weight:600;font-size:16px;line-height:30px;color:#2b2b2b;text-transform:uppercase}
.dots{position:absolute;top:653px;left:577px;display:flex;gap:8px}
.dots span{width:12px;height:12px;border-radius:50%;border:2px solid var(--white)}
.dots span.on{background:var(--white)}
.h2{font-family:"Montserrat",sans-serif;font-weight:700;font-size:37px;text-transform:uppercase}
.about-title{left:104px;top:810px;color:#3d3d3d}
.about-text{left:104px;top:874px;width:540px;font-size:12.5px;line-height:30px;color:var(--muted)}
.ticks{left:104px;top:958px;list-style:none;font-size:12.5px;color:var(--muted)}
.ticks li{height:37px;display:flex;align-items:center;gap:24px}
.btn{display:flex;align-items:center;justify-content:center;background:var(--orange);color:var(--white);border-radius:26px;font-family:"Montserrat",sans-serif;font-weight:700;font-size:14px;text-transform:uppercase}
.about-btn{left:107px;top:1200px;width:160px;height:48px}
.about-photo{left:710px;top:775px;width:520px;height:520px;border-radius:50%;border:8px solid var(--orange);background:radial-gradient(circle at 50% 55%,#ffffff 0%,#f1f1f1 60%,#dcdcdc 100%)}
.tile{background:#888;overflow:hidden}
.tile-rental{left:87px;top:1387px;width:543px;height:460px;background:linear-gradient(160deg,#6c6e6a,#b9bcb7 45%,#4e6a49 75%,#8f918c)}
.tile-tours{left:645px;top:1387px;width:468px;height:220px;background:linear-gradient(180deg,#9fc4de 0%,#d6e2e6 45%,#a79a72 75%,#c8b892)}
.tile-deals{left:645px;top:1627px;width:468px;height:220px;background:linear-gradient(120deg,#e8a93a,#f5cf6a 40%,#7d6a4a 80%,#4d4338)}
.tile-label{position:absolute;background:var(--label);color:var(--white);font-family:"Montserrat",sans-serif;font-weight:700;font-size:15px;text-transform:uppercase;padding:0 28px;height:46px;display:flex;align-items:center;white-space:nowrap}
.tile-rental .tile-label{left:0;top:382px}
.tile-tours .tile-label{left:0;top:153px}
.tile-deals .tile-label{left:0;top:153px}
.offer{left:0;top:1915px;width:1200px;height:468px;background:linear-gradient(180deg,#cfe0ee 0%,#eef3f7 55%,#f4f6f8 100%)}
.offer-photo{left:0;top:1915px;width:560px;height:468px;background:linear-gradient(180deg,rgba(207,224,238,0) 0%,rgba(207,224,238,0) 58%,#8a7458 78%,#5b4a38 100%)}
.offer-rider{left:120px;top:1935px;width:280px;height:330px;border-radius:40%;background:radial-gradient(ellipse at center,rgba(190,40,40,.55) 0%,rgba(60,60,70,.35) 45%,rgba(0,0,0,0) 70%)}
.offer-title{left:560px;top:2026px;color:#4a4a4a}
.offer-text{left:560px;top:2100px;width:490px;font-size:12.5px;line-height:28px;color:#8a8a8a}
.offer-btn{left:560px;top:2245px;width:158px;height:46px}
.video{left:223px;top:2458px;width:754px;height:395px;background:linear-gradient(180deg,#7a7a6a 0%,#a59258 45%,#5e5236 75%,#2a241a 100%)}
.play{position:absolute;left:336px;top:156px;width:82px;height:82px}
.kiwi{left:975px;top:2740px;width:220px;height:150px;border-radius:55% 45% 45% 55%/60% 60% 40% 40%;background:radial-gradient(ellipse at 55% 45%,#6b5540,#3e3024)}
.news{left:0;top:2910px;width:1200px;height:382px;background:var(--light)}
.news-title{left:0;top:2993px;width:1200px;text-align:center;color:#3d3d3d;font-size:35px}
.news-text{left:230px;top:3056px;width:740px;text-align:center;font-size:12.5px;line-height:30px;color:var(--muted)}
.news-form{left:242px;top:3146px;width:715px;height:49px;border-radius:26px;background:var(--white);border:1px solid #e2e2e2;overflow:hidden;display:flex}
.news-form .field{flex:1;padding-left:28px;display:flex;align-items:center;font-size:12px;color:#666}
.news-form .btn{width:126px;border-radius:0 26px 26px 0}
.foot{left:0;top:3292px;width:1200px;height:344px;background:var(--black)}
.foot .brand-badge{left:526px;top:10px;width:150px;height:150px;font-size:22px;border:6px solid var(--white)}
.foot-rule{position:absolute;left:87px;top:174px;width:1026px;height:1px;background:#2c2c2c}
.social{position:absolute;top:200px;left:0;width:1200px;height:60px}
.social span{position:absolute;top:0;width:60px;height:60px;border:1px solid #8a8a8a;border-radius:50%;display:flex;align-items:center;justify-content:center}
.copy{position:absolute;top:290px;left:0;width:1200px;text-align:center;font-size:12px;color:#c8c8c8}
</style>
</head>
<body>

<header class="abs head">
  <div class="brand-badge">RIDGEVOLT</div>
  <nav class="nav">
    <a class="active" style="left:0">Home</a>
    <a style="left:82px">About Us</a>
    <a style="left:188px">What We Offer</a>
    <a style="left:335px">Bookings</a>
    <a style="left:445px">Contact Us</a>
  </nav>
</header>

<section class="abs hero" role="img" aria-label="Rider on an e-mountain bike on a rocky ridge above mountains at sunset">
  <h1>RIDGEVOLT</h1>
  <p>Be offering bike rental &amp; guided tours around the Nelson region in New Zealand.</p>
  <div class="dots"><span class="on"></span><span></span><span></span></div>
</section>

<h2 class="abs h2 about-title">About Us</h2>
<p class="abs about-text">Sed ut perspiciatis unde omnis iste natus error sit voluptatem accusantium doloremque laudantium, inventore veritatis et quasi architecto beatae vitae dicta sunt explicabo.</p>
<ul class="abs ticks">
  <li><svg width="14" height="12" viewBox="0 0 14 12"><path d="M1 6.5l4 4L13 1.5" fill="none" stroke="#f15a1f" stroke-width="2.6"/></svg>Sed ut perspiciatis unde omnis iste natus error sit</li>
  <li><svg width="14" height="12" viewBox="0 0 14 12"><path d="M1 6.5l4 4L13 1.5" fill="none" stroke="#f15a1f" stroke-width="2.6"/></svg>voluptatem accusantium doloremque</li>
  <li><svg width="14" height="12" viewBox="0 0 14 12"><path d="M1 6.5l4 4L13 1.5" fill="none" stroke="#f15a1f" stroke-width="2.6"/></svg>laudantium, totam rem aperiam, eaque ipsa quae</li>
  <li><svg width="14" height="12" viewBox="0 0 14 12"><path d="M1 6.5l4 4L13 1.5" fill="none" stroke="#f15a1f" stroke-width="2.6"/></svg>ab illo inventore veritatis et quasi architecto</li>
  <li><svg width="14" height="12" viewBox="0 0 14 12"><path d="M1 6.5l4 4L13 1.5" fill="none" stroke="#f15a1f" stroke-width="2.6"/></svg>beatae vitae dicta sunt explicabo</li>
  <li><svg width="14" height="12" viewBox="0 0 14 12"><path d="M1 6.5l4 4L13 1.5" fill="none" stroke="#f15a1f" stroke-width="2.6"/></svg>voluptatem accusantium doloremque</li>
</ul>
<div class="abs btn about-btn">Read More</div>
<div class="abs about-photo" role="img" aria-label="Full-suspension electric mountain bike, side view"></div>

<div class="abs tile tile-rental" role="img" aria-label="Row of rental e-bikes parked in docking stands">
  <div class="tile-label">Bike Rental and Pricing</div>
</div>
<div class="abs tile tile-tours" role="img" aria-label="Group of riders with bikes on a coastal trail">
  <div class="tile-label">Guided Tours and Pricing</div>
</div>
<div class="abs tile tile-deals" role="img" aria-label="Rider's legs beside a bike on a sunny road">
  <div class="tile-label">Recommended Package Deals</div>
</div>

<section class="abs offer"></section>
<div class="abs offer-photo" role="img" aria-label="Mountain biker jumping off a rocky hilltop against the sky"></div>
<div class="abs offer-rider" aria-hidden="true"></div>
<h2 class="abs h2 offer-title">What We Offer</h2>
<p class="abs offer-text">Sed ut perspiciatis unde omnis iste natus error sit voluptatem accusantium doloremque laudantium, totam rem aperiam, eaque ipsa quae ab illo inventore veritatis et quasi architecto beatae vitae dicta sunt explicabo. Nemo enim ipsam voluptatem quia voluptas sit aspernat consequuntur magni dolores eos qui ratione voluptatem sequi nesciunt.</p>
<div class="abs btn offer-btn">Read More</div>

<div class="abs video" role="img" aria-label="Video still of a rider on a dusty trail at golden hour">
  <svg class="play" viewBox="0 0 82 82"><circle cx="41" cy="41" r="38" fill="rgba(0,0,0,.25)" stroke="#fff" stroke-width="3"/><path d="M33 26l24 15-24 15z" fill="none" stroke="#fff" stroke-width="3" stroke-linejoin="round"/></svg>
</div>
<div class="abs kiwi" role="img" aria-label="Kiwi bird standing beside the video"></div>

<section class="abs news"></section>
<h2 class="abs h2 news-title">Our Newsletter</h2>
<p class="abs news-text">Sed ut perspiciatis unde omnis iste natus error sit voluptatem accusantium doloremque laudantium, totam rem aperiam, eaque ipsa quae ab illo inventore veritatis et quasi architecto beatae vitae dicta sunt explicabo.</p>
<div class="abs news-form"><div class="field">Enter Your Email id :</div><div class="btn">Submit</div></div>

<footer class="abs foot">
  <div class="brand-badge">RIDGEVOLT</div>
  <div class="foot-rule"></div>
  <div class="social">
    <span style="left:389px"></span>
    <span style="left:462px"></span>
    <span style="left:532px"></span>
    <span style="left:605px"></span>
    <span style="left:675px"></span>
    <span style="left:748px"><svg width="18" height="14" viewBox="0 0 18 14"><rect x="1" y="1" width="16" height="12" fill="none" stroke="#fff" stroke-width="1.5"/><path d="M1 1l8 7 8-7" fill="none" stroke="#fff" stroke-width="1.5"/></svg></span>
  </div>
  <p class="copy">© Copyrights 2018 Ridgevolt All Rights Reserved.</p>
</footer>

</body>
</html>
```